Business Card Design

We need a design for business cards for our company. We have a logo. We teach EMT's and we are based out of Virginia. The information that will need to add would be, name, title, phone number, email, address. On the back of the business card would be "We help you, help others"

Target Market(s)

People that want to become EMT's

Colors

Designer to choose colors to be used in the design.

Requirements
Must have
• company logo

```html
<!DOCTYPE html>
<html lang="en">
<head>
<meta charset="utf-8">
<title>Medic Path Academy – Business Card</title>
<link rel="stylesheet" href="https://fonts.googleapis.com/css2?family=Montserrat:wght@500;600&family=Roboto:wght@400&display=swap">
<style>
  :root {
    --brand-red: #c01c2c;
    --brand-grey: #939598;
    --text-grey: #555759;
    --card-white: #ffffff;
    --stage: #d9d9d9;
  }
  * { box-sizing: border-box; margin: 0; padding: 0; }
  html, body { width: 1200px; height: 802px; overflow: hidden; }
  body { background: var(--stage); position: relative; font-family: "Roboto", Arial, sans-serif; }

  .card {
    position: absolute; top: 274px; width: 443px; height: 264px;
    overflow: hidden; box-shadow: 0 2px 6px rgba(0,0,0,0.25);
  }

  /* Front */
  .card--front { left: 136px; background: var(--card-white); }
  .front__band { position: absolute; left: 0; top: 0; width: 50px; height: 100%; background: var(--brand-red); }
  .front__rule { position: absolute; left: 52px; top: 0; width: 4px; height: 100%; background: var(--brand-grey); }
  .brand {
    position: absolute; right: 28px; top: 44px; display: flex; align-items: center; gap: 8px;
  }
  .brand__mark { width: 14px; height: 14px; border-radius: 50%; background: var(--brand-red); }
  .brand__name {
    font-family: "Montserrat", Arial, sans-serif; font-weight: 600; font-size: 21px;
    color: var(--brand-red); letter-spacing: 0.2px;
  }
  .contact { position: absolute; left: 80px; top: 132px; color: var(--text-grey); }
  .contact__name {
    font-family: "Montserrat", Arial, sans-serif; font-weight: 600; font-size: 16px;
    color: var(--brand-red); line-height: 1.1;
  }
  .contact__title { font-size: 13px; line-height: 1.1; }
  .contact__lines { margin-top: 10px; font-size: 13px; line-height: 16px; }
  .contact__line { display: flex; align-items: center; gap: 3px; }
  .contact__line svg { width: 12px; height: 10px; fill: var(--brand-red); }
  .contact__address { margin-top: 9px; font-size: 13px; line-height: 16px; }

  /* Back */
  .card--back { left: 624px; background: var(--brand-red); }
  .back__art {
    position: absolute; left: 0; top: 0; width: 100%; height: 100%;
    background: linear-gradient(135deg, var(--brand-grey) 0%, var(--brand-grey) 48%, var(--brand-red) 62%);
  }
  .back__tagline {
    position: absolute; right: 26px; top: 27px; text-align: left;
    font-family: "Montserrat", Arial, sans-serif; font-weight: 500; font-size: 25px;
    line-height: 32px; color: var(--card-white); letter-spacing: -0.3px;
  }
</style>
</head>
<body>

  <section class="card card--front">
    <div class="front__band"></div>
    <div class="front__rule"></div>

    <div class="brand">
      <span class="brand__mark"></span>
      <span class="brand__name">MEDIC PATH ACADEMY</span>
    </div>

    <div class="contact">
      <p class="contact__name">DANIEL HARPER</p>
      <p class="contact__title">Managing Director</p>
      <div class="contact__lines">
        <p class="contact__line">
          <svg viewBox="0 0 12 10" aria-hidden="true"><path d="M1 3 Q6 0 11 3 L10 4.5 L8 4 L8 3 Q6 2.3 4 3 L4 4 L2 4.5 Z M3 5 H9 L10.5 9.5 H1.5 Z"/></svg>
          555-014 2368
        </p>
        <p class="contact__line">
          <svg viewBox="0 0 12 10" aria-hidden="true"><path d="M0 1 H12 V9 H0 Z" /><path d="M0.5 1.5 L6 5.5 L11.5 1.5" stroke="#fff" stroke-width="1" fill="none"/></svg>
          hello@medicpath.com
        </p>
      </div>
      <p class="contact__address">18, Linden Street Suite 4<br>23219,Virginia USA</p>
    </div>
  </section>

  <section class="card card--back">
    <div class="back__art" role="img" aria-label="Stethoscope with medical cross and heartbeat line illustration"></div>
    <p class="back__tagline">WE HELP YOU<br>HELP OTHERS</p>
  </section>

</body>
</html>
```